Cat-products company needs smart, yet endearing, business card

We need a business card design for a new, but up-and-running, business based in Honolulu, Hawaii. The business is Purrnest Nook Co. Our first product is the most environmentally-friendly cat grass kit ever seen on the planet. Future products, currently in the R&D phase, will include a variety of exciting cat scratchers. We also do consulting work to help apartment-dwellers make their home more cat-friendly and, in the future, plan on doing full, custom installs of structure to create high walkways for cats.

Target Market(s)

Middle-aged, apartment-dwelling, middle-class workers who own 1 or more cats and who dote on them.

Industry/Entity Type

Pet Care

Contact Information for Business Card

A striking, professional, yet warm and friendly design is what we're after.

Font styles to use
Serif
Sans Serif
Other font styles liked:
• Comfortaa

Colors

Designer to choose colors to be used in the design.

Requirements
Must have
• The company logo: (see attachment)
• The company name: Purrnest Nook Co
• The web address: www.purrnestnookco.com
• Email: support@purrnestnookco.com
• Phone: +1 (808) 571 6023
• Update (Fri Jun 30 3017 7:45pm Hawaii Time) I would like, is possible, uploaded picture of the cat grass kit on the back of the card with some text along the lines of: Purrnest Nook Co - Maker Of The Leafiest Feline Sprout Set Yet
Nice to have
• A cat picture, cartoon, real or silhouette that illustrates cats in action and/or relaxing; ie using the apartment space to live, play and relax in and being well-contented.
• Most of the website is done in the font: Comfortaa. It might be nice to continue using this for brand consistency.
Should not have
• Hard-to-read fonts.

```html
<!DOCTYPE html>
<html lang="en">
<head>
<meta charset="utf-8">
<title>Purrnest Nook Co — Business Card</title>
<link rel="stylesheet" href="https://fonts.googleapis.com/css2?family=Comfortaa:wght@400;700&display=swap">
<style>
  :root {
    --backdrop: #3a3a3c;
    --card: #ffffff;
    --accent: #f5a812;
    --brand-dark: #4a2a22;
    --ink: #4b4b4b;
    --ink-soft: #6a6a6a;
    --paw-grey: #9a9a9a;
  }
  * { box-sizing: border-box; margin: 0; padding: 0; }
  html, body {
    width: 1200px; height: 1000px; overflow: hidden;
    background: var(--backdrop);
    font-family: "Comfortaa", "Trebuchet MS", sans-serif;
  }
  .stage { position: relative; width: 1200px; height: 1000px; }
  .card {
    position: absolute; left: 220px; width: 760px; height: 434px;
    background: var(--card);
    box-shadow: 0 10px 30px rgba(0,0,0,.45);
    overflow: hidden;
  }
  .card--front { top: 50px; }
  .card--back { top: 516px; }

  /* Front */
  .paw-pattern {
    position: absolute; inset: 0;
    background:
      radial-gradient(circle at 15% 25%, rgba(246,196,206,.55), transparent 22%),
      radial-gradient(circle at 35% 55%, rgba(196,182,226,.55), transparent 20%),
      radial-gradient(circle at 70% 15%, rgba(190,210,240,.55), transparent 20%),
      radial-gradient(circle at 80% 55%, rgba(246,200,206,.5), transparent 22%),
      radial-gradient(circle at 25% 85%, rgba(250,226,186,.55), transparent 20%),
      radial-gradient(circle at 50% 85%, rgba(190,214,240,.5), transparent 18%),
      radial-gradient(circle at 92% 30%, rgba(200,228,200,.5), transparent 18%),
      radial-gradient(circle at 10% 60%, rgba(252,240,200,.55), transparent 18%),
      #ffffff;
  }
  .brand {
    display: flex; align-items: center; gap: 10px;
    font-weight: 700; color: var(--accent); letter-spacing: .5px;
  }
  .brand__mark { background: var(--brand-dark); flex: none; }
  .card--front .brand {
    position: absolute; left: 50%; top: 50%; transform: translate(-50%, -50%);
    font-size: 34px;
  }
  .card--front .brand__mark { width: 30px; height: 30px; }

  /* Back */
  .paw-trail {
    position: absolute; left: 50px; top: 20px; width: 300px; height: 230px;
    background: linear-gradient(35deg, rgba(154,154,154,0) 20%, rgba(154,154,154,.22) 60%, rgba(154,154,154,.32) 100%);
    clip-path: polygon(0 100%, 18% 100%, 100% 10%, 100% 0, 80% 0);
  }
  .card--back .brand {
    position: absolute; right: 40px; top: 70px; font-size: 26px;
  }
  .card--back .brand__mark { width: 22px; height: 22px; }

  .person { position: absolute; left: 90px; top: 250px; }
  .person__name { font-size: 30px; font-weight: 700; color: var(--accent); }
  .person__role { font-size: 18px; color: var(--ink-soft); margin-top: 4px; }

  .address {
    position: absolute; left: 110px; top: 322px;
    font-size: 17px; line-height: 24px; color: var(--ink); font-style: normal;
  }
  .contact {
    position: absolute; left: 110px; top: 378px; list-style: none;
    font-size: 17px; line-height: 26px; color: var(--ink);
  }
  .contact li { display: flex; align-items: center; gap: 12px; }
  .contact svg { width: 16px; height: 16px; fill: var(--accent); flex: none; }

  .web {
    position: absolute; right: 44px; top: 300px; font-size: 17px; color: var(--ink);
  }
  .web__domain { color: var(--accent); }
  .web-bar {
    position: absolute; right: 40px; top: 340px; width: 210px; height: 12px;
    background: var(--accent);
  }
</style>
</head>
<body>
<main class="stage">
  <section class="card card--front" aria-label="Card front">
    <div class="paw-pattern" role="img" aria-label="Scattered pastel paw-print pattern"></div>
    <div class="brand"><span class="brand__mark"></span>Purrnest Nook Co</div>
  </section>

  <section class="card card--back" aria-label="Card back">
    <div class="paw-trail" role="img" aria-label="Trail of small grey paw prints"></div>
    <div class="brand"><span class="brand__mark"></span>Purrnest Nook Co</div>

    <div class="person">
      <p class="person__name">Nalani Kealoha</p>
      <p class="person__role">Director</p>
    </div>

    <address class="address">Your Street Address,<br>Country,1234</address>

    <ul class="contact">
      <li>
        <svg viewBox="0 0 24 24" aria-hidden="true"><path d="M6.6 10.8a15 15 0 0 0 6.6 6.6l2.2-2.2a1 1 0 0 1 1-.25 11.4 11.4 0 0 0 3.6.57 1 1 0 0 1 1 1V20a1 1 0 0 1-1 1A17 17 0 0 1 3 4a1 1 0 0 1 1-1h3.5a1 1 0 0 1 1 1c0 1.25.2 2.45.57 3.57a1 1 0 0 1-.25 1z"/></svg>
        <span>+1 (808) 571 6023</span>
      </li>
      <li>
        <svg viewBox="0 0 24 24" aria-hidden="true"><path d="M2 5h20v14H2z M2 5l10 8 10-8" /></svg>
        <span>support@purrnestnookco.com</span>
      </li>
    </ul>

    <p class="web">www.<span class="web__domain">purrnestnookco</span>.com</p>
    <div class="web-bar"></div>
  </section>
</main>
</body>
</html>
```